Brochure for a website accessibility report

This brochure is related to a report that www.qelvantrix.org sell. The report shows the results of an automated audit of a websites accessibility. It shows details of issues found with screen shots, examples of code and provides remediation advice.

The brochure will be a pdf 8.5 inches by 11 inches. It can be anywhere from 6 to 10 pages.

The FlintVue™ name itself should be “Bree Serif” font. The fonts, styles, colors and sizes are up to you.

The images used and logo of the Office of Digital Reachworks and K7P logo are upload

We highlighted in blue page extracts from the report we sell. Do not use the blue highlight, it is merely there to show you where the specific examples of the report we sell are vs the other content in the report. The areas in blue which show the content from the actual report should be shown as an extract of the actual page of the report. You have flexibility to change the layout and the way the content look.

The red square callouts over the blue content are callouts that describe the specific page extracts. We used it as a red callout only so that you would be able to see it. You should change the specific location, look and feel of the callout to be appropriate

Target Market(s)

Marketing and Technical people

Industry/Entity Type

Information Technology

Font styles to use
Sans Serif

Colors

Designer to choose colors to be used in the design.

Requirements
Should not have
• wheelchairs, images of blind people

```html
<!DOCTYPE html>
<html lang="en">
<head>
<meta charset="utf-8">
<title>FlintVue™ Brochure 2019 – Page 9</title>
<link href="https://fonts.googleapis.com/css2?family=Bree+Serif&family=Montserrat:wght@400;500;700;800&family=Courier+Prime&display=swap" rel="stylesheet">
<style>
  :root {
    --green: #25b170;
    --orange: #ff6600;
    --cream: #fdf3e3;
    --ink: #111111;
    --link: #1aa3e8;
    --rule: #e2e2e2;
    --code: #555555;
    --paper: #ffffff;
  }
  * { margin: 0; padding: 0; box-sizing: border-box; }
  html, body { width: 972px; height: 1200px; overflow: hidden; background: var(--paper); }
  body { font-family: "Montserrat", sans-serif; color: var(--ink); }
  .page { position: relative; width: 972px; height: 1200px; background: var(--paper); }
  .side-band { position: absolute; left: 0; top: 0; }

  .masthead { position: absolute; left: 261px; top: 60px; }
  .masthead .product { font-family: "Bree Serif", serif; font-size: 17px; line-height: 18px; }
  .masthead .edition { font-family: "Montserrat", sans-serif; font-weight: 800; font-size: 17px; color: var(--green); line-height: 20px; }
  .masthead-rule { position: absolute; left: 261px; top: 113px; width: 434px; height: 2px; background: var(--rule); }

  .brand { position: absolute; right: 67px; top: 66px; display: flex; align-items: center; gap: 8px; }
  .brand-dot { width: 12px; height: 12px; border-radius: 50%; background: var(--green); flex: none; }
  .brand-name { font-family: "Montserrat", sans-serif; font-weight: 700; font-size: 13px; line-height: 16px; color: var(--ink); }

  .issue-title { position: absolute; left: 261px; top: 172px; font-size: 25px; font-weight: 800; white-space: nowrap; letter-spacing: -0.2px; }
  .issue-title .label { color: var(--green); }
  .issue-lead { position: absolute; left: 261px; top: 210px; font-size: 14px; font-weight: 700; }
  .issue-body { position: absolute; left: 261px; top: 238px; width: 644px; font-size: 14.6px; line-height: 20px; text-align: justify; }
  .issue-body a { color: var(--link); text-decoration: none; }

  .callout { position: absolute; left: 263px; width: 642px; background: var(--orange); color: #fff; font-weight: 700; font-size: 13.4px; line-height: 16px; padding: 10px 10px 0; }
  .callout-top { top: 336px; height: 48px; }
  .callout-top::before { content: ""; position: absolute; right: 18px; top: -8px; border: 8px solid transparent; border-top: 0; border-bottom-color: var(--orange); }
  .callout-bottom { top: 638px; height: 52px; left: 261px; width: 644px; }
  .callout-bottom::after { content: ""; position: absolute; left: 22px; bottom: -8px; border: 9px solid transparent; border-bottom: 0; border-top-color: var(--orange); }

  .section-heading { position: absolute; left: 261px; font-size: 19px; font-weight: 800; }
  .remedy-heading { top: 406px; }
  .remedy-body { position: absolute; left: 261px; top: 436px; width: 644px; font-size: 14.6px; line-height: 18.3px; text-align: justify; }
  .reading-heading { top: 541px; }
  .reading-rule { position: absolute; left: 489px; top: 555px; width: 416px; height: 1px; background: var(--orange); }

  .reading-card { position: absolute; top: 573px; width: 306px; height: 40px; background: var(--cream); display: flex; align-items: center; gap: 8px; padding-left: 12px; font-weight: 800; font-size: 15px; }
  .reading-card.first { left: 261px; }
  .reading-card.second { left: 599px; }

  .example-label { position: absolute; left: 261px; top: 703px; font-size: 12px; font-weight: 700; }
  .example-url { position: absolute; left: 261px; top: 721px; font-size: 12px; color: var(--link); letter-spacing: -0.3px; }
  .screenshot { position: absolute; left: 261px; top: 745px; width: 306px; height: 330px; background: linear-gradient(180deg, #1b2a4a 0%, #c9b27a 10%, #eef0f4 22%, #ffffff 60%, #14284a 88%, #0f2040 100%); }

  .issue-panel { position: absolute; left: 599px; top: 704px; width: 306px; height: 371px; background: var(--cream); padding: 14px 16px 0 17px; }
  .panel-heading { font-size: 13px; font-weight: 800; line-height: 16px; }
  .panel-text { font-size: 11.2px; line-height: 14.6px; margin-top: 1px; }
  .code-heading { margin-top: 13px; }
  .code-snippet { font-family: "Courier Prime", monospace; font-size: 10.6px; line-height: 14.6px; color: var(--code); margin-top: 2px; white-space: pre; }

  .footer-site { position: absolute; left: 261px; top: 1142px; font-size: 14px; font-weight: 500; }
  .footer-rule { position: absolute; left: 412px; top: 1153px; width: 484px; height: 1px; background: var(--green); }
  .page-number { position: absolute; left: 910px; top: 1143px; font-size: 13px; color: var(--green); }
</style>
</head>
<body>
<main class="page">
  <svg class="side-band" width="170" height="1200" viewBox="0 0 170 1200" aria-hidden="true">
    <polygon points="0,85 169,177 169,1076 0,1167" fill="var(--green)"/>
  </svg>

  <header>
    <div class="masthead">
      <div class="product">FlintVue™</div>
      <div class="edition">Brochure 2019</div>
    </div>
    <div class="masthead-rule"></div>
    <div class="brand">
      <span class="brand-dot"></span>
      <span class="brand-name">Office of Digital<br>Reachworks</span>
    </div>
  </header>

  <h1 class="issue-title"><span class="label">Issue:</span> Layout Table with Summary (priority 4)</h1>
  <p class="issue-lead">The summary attribute on a layout table should be empty.</p>
  <p class="issue-body">The purpose of a layout table is simply to control the placement of content; the table itself is transparent to the user. A summary attribute would break this transparency by calling attention to the table. A null summary (summary=””) on layout tables is acceptable. Issue is relevant to checkpoint: <a href="#">1.3.1 (A)</a></p>

  <div class="callout callout-top">Actual screen shots of your website pages are shown so you can see exactly where the “Issues Discovered” are present</div>

  <h2 class="section-heading remedy-heading">General Remediation Advice:</h2>
  <p class="remedy-body">Remove the summary attribute from tables used solely for layout. It should only be used for tables that present tabular data. In HTML 5, you can use the role attribute on the TABLE with a value of “presentation” to explicitly mark the table as being used for layout.</p>

  <h2 class="section-heading reading-heading">Suggested Reading:</h2>
  <div class="reading-rule"></div>
  <div class="reading-card first">
    <svg width="14" height="14" viewBox="0 0 14 14" aria-hidden="true"><circle cx="7" cy="7" r="7" fill="var(--orange)"/><path d="M6 4l3 3-3 3" stroke="#fff" stroke-width="1.6" fill="none"/></svg>
    Adaptable
  </div>
  <div class="reading-card second">
    <svg width="14" height="14" viewBox="0 0 14 14" aria-hidden="true"><circle cx="7" cy="7" r="7" fill="var(--orange)"/><path d="M6 4l3 3-3 3" stroke="#fff" stroke-width="1.6" fill="none"/></svg>
    Info and Relationships
  </div>

  <div class="callout callout-bottom">Appropriate screenshots with the issue highlighted are shown where the issue resides on the webpage</div>

  <p class="example-label">Example 1 of 6:</p>
  <p class="example-url">http://www.norvaleum.org/es/archivo/cm/cartas.shtml</p>
  <div class="screenshot" role="img" aria-label="Screenshot of the audited web page with the layout table highlighted"></div>

  <aside class="issue-panel">
    <h3 class="panel-heading">SPECIFIC ISSUE:</h3>
    <p class="panel-text">Layout tables should not have a ‘SUMMARY’ attribute; or it should be an empty text value. &lt;TABLE&gt; Tag found summary=’La tabla debe ser leída por fila. Tiene tres filas, cada una representa u...</p>
    <h3 class="panel-heading code-heading">CODE SNIPPET</h3>
    <p class="code-snippet">&lt;table class=”yrlist” summary=”-
La tabla debe ser le&amp;#237;da por
fila. Tiene tres filas, cada una
representa una d&amp;#233;cada, la
fila de arriba es de la d&amp;#233;ca-
da actual. Los v&amp;#237;nculos de los
a&amp;#241;os en cada celda de la tabla
abrir&amp;#225;n una p&amp;#225;gina con
la lista de cartas intercambiadas
durante ese a&amp;#241;o en particu-
lar.”&gt; &lt;tbody&gt;&lt;tr&gt; &lt;th colspan=”11”
class=”tbltitle”&gt;Intercambio de
cartas del Director Ejecutivo y
la Presidenta del Comité
Norvaleum&lt;/th&gt;</p>
  </aside>

  <footer>
    <p class="footer-site">www.qelvantrix.org</p>
    <div class="footer-rule"></div>
    <p class="page-number">9</p>
  </footer>
</main>
</body>
</html>
```